Business Card Re-Design/Update

We'd like to update out business cards. I've included our current "Style guide" which has the colour scheme of the organisation in it. I've also included the branding files with logos etc in them.

I've also included a copy of one of our existing cards so that you can see how ugly/dated they look. I'd like a fresh modern corporate look.

Target Market(s)

These are for our clients, potential clients, industry contacts - like all business cards

Contact Information for Business Card

Name
Position
Company Address - Level 1, 47 Fernby Street, Carlow Qld 4072
Direct Phone
mobile
Email
Website -www.korvalit.com.au
Logo

Colors

Designer to choose colors to be used in the design.

Requirements
Must have
• Main Logo
• Cards will need to be editable to be able to personalize them for each new employee.
Nice to have
• The MapOut, ShipWell, KeepSteady would be okay to have if they can be sensibly and professionally added to the look without detracting from the main imagery.
• Maybe they could go on the back of the card? will leave this to your creative discretion as to whether/where they fit.
Should not have
• Should not have decorative or script fonts

```html
<!DOCTYPE html>
<html lang="en">
<head>
<meta charset="utf-8">
<title>Korvalit Business Card</title>
<link rel="stylesheet" href="https://fonts.googleapis.com/css2?family=Lato:wght@400;700;900&family=Oswald:wght@500&display=swap">
<style>
  :root {
    --backdrop: #2b2b2d;
    --brand-red: #d0202a;
    --brand-red-dark: #a3121b;
    --band-text: #7e0d13;
    --ink: #2e2e30;
    --ink-soft: #4a4a4c;
    --paper: #f7f7f7;
    --divider: #8a8a8a;
  }
  * { box-sizing: border-box; margin: 0; padding: 0; }
  html, body { width: 1200px; height: 997px; overflow: hidden; }
  body {
    background: var(--backdrop);
    font-family: "Lato", Arial, sans-serif;
    position: relative;
  }
  .card {
    position: absolute;
    width: 700px;
    height: 400px;
    border-radius: 4px;
    overflow: hidden;
    box-shadow: 0 18px 40px rgba(0,0,0,.55);
  }
  /* Back of card */
  .card-back { left: 250px; top: 60px; }
  .card-back .pattern {
    position: absolute; inset: 0;
    background: linear-gradient(135deg, #e0333a 0%, #c81f28 45%, #b5151e 100%);
  }
  .card-back .brand {
    position: absolute; left: 0; right: 0; top: 140px;
    display: flex; align-items: center; justify-content: center; gap: 18px;
  }
  .brand-square { width: 46px; height: 46px; background: #ffffff; }
  .card-back .brand-name {
    font-weight: 700; font-size: 74px; color: #2b2b2d; letter-spacing: -1px; line-height: 1;
  }
  .card-back .web {
    position: absolute; left: 0; right: 0; top: 262px;
    text-align: center; color: #ffffff; font-weight: 700;
    font-size: 17px; letter-spacing: 7px; text-transform: uppercase;
  }
  /* Front of card */
  .card-front { left: 250px; top: 520px; background: var(--paper); }
  .card-front .watermark-block {
    position: absolute; right: 40px; top: 40px; width: 190px; height: 190px;
    background: rgba(208,32,42,.08);
  }
  .card-front .brand {
    position: absolute; left: 60px; top: 58px;
    display: flex; align-items: center; gap: 14px;
  }
  .card-front .brand-square { width: 40px; height: 40px; background: var(--brand-red); }
  .card-front .brand-name {
    font-weight: 700; font-size: 56px; color: var(--ink); letter-spacing: -1px; line-height: 1;
  }
  .divider {
    position: absolute; left: 360px; top: 150px; width: 2px; height: 120px;
    background: linear-gradient(to bottom, transparent, var(--divider), transparent);
  }
  .person { position: absolute; right: 360px; top: 196px; text-align: right; }
  .person-name {
    font-family: "Oswald", Arial, sans-serif; font-weight: 500;
    font-size: 22px; color: var(--brand-red); text-transform: uppercase; letter-spacing: .5px;
  }
  .person-role { font-size: 15px; color: var(--ink-soft); margin-top: 2px; }
  .contacts { position: absolute; left: 390px; top: 152px; list-style: none; }
  .contacts li {
    display: flex; align-items: center; gap: 10px;
    font-size: 16px; color: var(--ink); height: 29px;
  }
  .contacts .note { font-size: 12px; color: var(--ink-soft); margin-left: 4px; }
  .icon {
    width: 20px; height: 20px; border-radius: 50%;
    background: var(--brand-red); display: flex; align-items: center; justify-content: center;
    flex: none;
  }
  .icon svg { width: 12px; height: 12px; fill: #ffffff; }
  .address-band {
    position: absolute; left: 0; right: 0; bottom: 0; height: 56px;
    background: var(--brand-red);
    display: flex; align-items: center; justify-content: center;
    font-weight: 900; font-size: 17px; color: var(--band-text); letter-spacing: .3px;
  }
</style>
</head>
<body>

<section class="card card-back" aria-label="Card back">
  <div class="pattern" role="img" aria-label="Red faceted low-poly background texture"></div>
  <div class="brand">
    <span class="brand-square"></span>
    <span class="brand-name">korvalit</span>
  </div>
  <p class="web">www.korvalit.com.au</p>
</section>

<section class="card card-front" aria-label="Card front">
  <div class="watermark-block"></div>
  <div class="brand">
    <span class="brand-square"></span>
    <span class="brand-name">korvalit</span>
  </div>

  <div class="divider"></div>

  <div class="person">
    <p class="person-name">Maren Holt</p>
    <p class="person-role">Business Development Manager</p>
  </div>

  <ul class="contacts">
    <li>
      <span class="icon"><svg viewBox="0 0 12 12"><path d="M1 4c0-2 2-3 5-3s5 1 5 3l-2 1-1-1H4L3 5 1 4zM3 6h6l1 5H2l1-5z"/></svg></span>
      +61 (0)412 555 018
    </li>
    <li>
      <span class="icon"><svg viewBox="0 0 12 12"><path d="M3 1h6v3H3zM1 5h10v4H9v2H3V9H1zM4 8v2h4V8z"/></svg></span>
      +61 (0)7 3555 0142
    </li>
    <li>
      <span class="icon"><svg viewBox="0 0 12 12"><path d="M2.5 1 4.5 1 5.5 4 4 5c.6 1.3 1.7 2.4 3 3l1-1.5 3 1V10.5c0 .5-.5 1-1 1C5 11.5.5 7 .5 2c0-.5.5-1 1-1z"/></svg></span>
      +61 (0)7 3555 0157 <span class="note">(Direct)</span>
    </li>
    <li>
      <span class="icon"><svg viewBox="0 0 12 12"><path d="M1 3h10v.6L6 7 1 3.6zM1 4.8 6 8.2l5-3.4V9H1z"/></svg></span>
      mholt@korvalit.com.au
    </li>
  </ul>

  <div class="address-band">18/6 Tallis Grove Road, Carlow QLD 4072</div>
</section>

</body>
</html>
```